Brookmere Osteopathy flyer

I want a clean clear DL flyer (but also want an A4 poster) promoting a new Osteopathic business in a semi rural area in Tasmania (Australia).
It can have pictures like the examples attached to show people what Osteopathy is (its like Chiropractic and physiotherapy).
I am the sole practioner and am male, so any pictures would be best to be a white male if possible.
I've attached some wording, you can use all, or none of it
I don't have a phone number for the business yet
info@brookmereosteopathy.example
www.brookmereosteopathy.example
Target Market(s)
Australians, from tradies, professionals, babies to retired people
Industry/Entity Type
Health
Look and feel

```html
<!DOCTYPE html>
<html lang="en">
<head>
<meta charset="utf-8">
<title>Brookmere Osteopathy Flyer</title>
<link rel="stylesheet" href="https://fonts.googleapis.com/css2?family=Open+Sans:wght@700&family=Poppins:wght@400&display=swap">
<style>
  :root {
    --slate: #41565f;
    --blue: #0d96d2;
    --blue-pill: #40bbee;
    --blue-faint: #24a7e0;
    --orange: #e67e22;
    --orange-light: #f3b27a;
    --orange-photo-a: #f0a45a;
    --orange-photo-b: #c77a35;
    --white: #ffffff;
  }
  * { margin: 0; padding: 0; box-sizing: border-box; }
  html, body { width: 911px; height: 1200px; overflow: hidden; }
  body { background: var(--slate); position: relative; font-family: "Poppins", sans-serif; }
  .flyer {
    position: absolute; left: 107px; top: 77px;
    width: 697px; height: 1046px;
    background: var(--blue); overflow: hidden;
  }
  .flyer-shapes { position: absolute; inset: 0; }
  .brand {
    position: absolute; left: 235px; top: 24px;
    width: 228px; height: 228px;
    border: 2px solid var(--white); border-radius: 50%;
    display: flex; align-items: center; justify-content: center;
  }
  .brand-name {
    color: var(--white); font-weight: 400;
    font-size: 20px; letter-spacing: 2px; text-align: center; line-height: 1.3;
    text-transform: uppercase;
  }
  .title-pill {
    position: absolute; left: 16px; top: 552px; width: 666px; height: 93px;
    border-radius: 47px; background: var(--blue-pill);
    display: flex; align-items: center; justify-content: center;
  }
  .title-pill h1 {
    font-family: "Open Sans", sans-serif; font-weight: 700; font-size: 23.6px;
    color: var(--white); letter-spacing: 0.1px;
  }
  .reasons { list-style: none; position: absolute; top: 0; left: 0; }
  .reason {
    position: absolute; color: var(--white); font-size: 14.2px; line-height: 1;
    display: flex; align-items: center; white-space: nowrap;
  }
  .reason svg { width: 25px; height: 25px; margin-right: 7px; flex: none; }
  .intro {
    position: absolute; left: 66px; width: 565px; top: 836px;
    color: var(--white); font-size: 12px; line-height: 18px; text-align: center;
  }
  .contacts { font-style: normal; }
  .contact {
    position: absolute; color: var(--white); font-size: 11px;
    display: flex; align-items: center; white-space: nowrap;
  }
  .contact svg { width: 11px; height: 11px; margin-right: 8px; flex: none; }
</style>
</head>
<body>
<main class="flyer">
  <svg class="flyer-shapes" width="697" height="1046" viewBox="0 0 697 1046">
    <defs>
      <linearGradient id="heroTone" x1="0" y1="0" x2="1" y2="1">
        <stop offset="0" stop-color="var(--orange-photo-a)"/>
        <stop offset="0.6" stop-color="#e9934a"/>
        <stop offset="1" stop-color="var(--orange-photo-b)"/>
      </linearGradient>
      <linearGradient id="clinicTone" x1="0" y1="0" x2="0" y2="1">
        <stop offset="0" stop-color="#eceef0"/>
        <stop offset="0.45" stop-color="#9a9ea3"/>
        <stop offset="0.7" stop-color="#d7dff0"/>
        <stop offset="1" stop-color="#c9b9a2"/>
      </linearGradient>
      <radialGradient id="practitionerTone" cx="0.5" cy="0.35" r="0.7">
        <stop offset="0" stop-color="#c9a58e"/>
        <stop offset="0.35" stop-color="#8c9a92"/>
        <stop offset="0.7" stop-color="#6f7f78"/>
        <stop offset="1" stop-color="#eef2f6"/>
      </radialGradient>
      <linearGradient id="babyTone" x1="0" y1="0" x2="0" y2="1">
        <stop offset="0" stop-color="#dcd8e2"/>
        <stop offset="0.45" stop-color="#e9c9b8"/>
        <stop offset="0.7" stop-color="#5aa7d6"/>
        <stop offset="1" stop-color="#e2e4ec"/>
      </linearGradient>
    </defs>

    <path class="hero-photo" role="img" aria-label="Photo of an osteopath's hands treating a patient's shoulder and neck, orange tinted"
          d="M0,0 H697 V265 Q348,520 0,247 Z" fill="url(#heroTone)"/>

    <circle class="faint-dot" cx="104" cy="530" r="64" fill="var(--blue-faint)"/>
    <circle class="faint-dot" cx="596" cy="698" r="64" fill="var(--blue-faint)"/>

    <circle cx="108" cy="335" r="91" fill="var(--white)"/>
    <circle role="img" aria-label="Photo of a woman lying on a treatment table receiving shoulder mobilisation" cx="108" cy="335" r="87" fill="url(#clinicTone)"/>

    <circle cx="343" cy="407" r="130" fill="var(--white)"/>
    <circle role="img" aria-label="Portrait photo of the practitioner in a white coat with a stethoscope" cx="343" cy="407" r="126" fill="url(#practitionerTone)"/>

    <circle cx="590" cy="356" r="94" fill="var(--white)"/>
    <circle role="img" aria-label="Photo of gentle hands cradling a sleeping newborn's head" cx="590" cy="356" r="90" fill="url(#babyTone)"/>

    <path class="footer-band" d="M0,1046 Q348,742 697,1046 Z" fill="var(--orange)"/>
    <path class="footer-band" d="M4,1046 Q348,758 693,1046 Z" fill="var(--white)"/>
    <path class="footer-band" d="M14,1046 Q348,776 683,1046 Z" fill="var(--orange)"/>
  </svg>

  <div class="brand"><p class="brand-name">Brookmere<br>Osteopathy</p></div>

  <div class="title-pill"><h1>COMMON REASONS PEOPLE VISIT AN OSTEOPATH</h1></div>

  <ul class="reasons">
    <li class="reason" style="left:50px;top:671px"><svg viewBox="0 0 25 25"><circle cx="11" cy="14" r="11" fill="var(--orange)"/><path d="M5,13 L10,19 L23,3" fill="none" stroke="var(--white)" stroke-width="2"/></svg>Back / neck pain</li>
    <li class="reason" style="left:50px;top:700px"><svg viewBox="0 0 25 25"><circle cx="11" cy="14" r="11" fill="var(--orange)"/><path d="M5,13 L10,19 L23,3" fill="none" stroke="var(--white)" stroke-width="2"/></svg>Headaches / migraines</li>
    <li class="reason" style="left:50px;top:734px"><svg viewBox="0 0 25 25"><circle cx="11" cy="14" r="11" fill="var(--orange)"/><path d="M5,13 L10,19 L23,3" fill="none" stroke="var(--white)" stroke-width="2"/></svg>Joint and muscle pain</li>
    <li class="reason" style="left:50px;top:762px"><svg viewBox="0 0 25 25"><circle cx="11" cy="14" r="11" fill="var(--orange)"/><path d="M5,13 L10,19 L23,3" fill="none" stroke="var(--white)" stroke-width="2"/></svg>Pregnancy-related discomfort</li>
    <li class="reason" style="left:50px;top:796px"><svg viewBox="0 0 25 25"><circle cx="11" cy="14" r="11" fill="var(--orange)"/><path d="M5,13 L10,19 L23,3" fill="none" stroke="var(--white)" stroke-width="2"/></svg>Disc related issues</li>
    <li class="reason" style="left:370px;top:671px"><svg viewBox="0 0 25 25"><circle cx="11" cy="14" r="11" fill="var(--orange)"/><path d="M5,13 L10,19 L23,3" fill="none" stroke="var(--white)" stroke-width="2"/></svg>Sciatica</li>
    <li class="reason" style="left:370px;top:700px"><svg viewBox="0 0 25 25"><circle cx="11" cy="14" r="11" fill="var(--orange)"/><path d="M5,13 L10,19 L23,3" fill="none" stroke="var(--white)" stroke-width="2"/></svg>Plantar fasciitis</li>
    <li class="reason" style="left:370px;top:734px"><svg viewBox="0 0 25 25"><circle cx="11" cy="14" r="11" fill="var(--orange)"/><path d="M5,13 L10,19 L23,3" fill="none" stroke="var(--white)" stroke-width="2"/></svg>Tendonitis / Bursitis</li>
    <li class="reason" style="left:370px;top:762px"><svg viewBox="0 0 25 25"><circle cx="11" cy="14" r="11" fill="var(--orange)"/><path d="M5,13 L10,19 L23,3" fill="none" stroke="var(--white)" stroke-width="2"/></svg>Adhesive capsulitis (frozen shoulder)</li>
    <li class="reason" style="left:370px;top:796px"><svg viewBox="0 0 25 25"><circle cx="11" cy="14" r="11" fill="var(--orange)"/><path d="M5,13 L10,19 L23,3" fill="none" stroke="var(--white)" stroke-width="2"/></svg>Tennis / Golfers elbow</li>
  </ul>

  <p class="intro">Osteopaths use a combination of joint manipulation, targeted deep tissue massage and stretching to improve function, relieve pain and support the body’s ability to heal itself.</p>

  <address class="contacts">
    <span class="contact" style="left:137px;top:981px"><svg viewBox="0 0 12 12"><path d="M6,0.5 A4,4 0 0 1 10,4.5 C10,7.5 6,11.5 6,11.5 C6,11.5 2,7.5 2,4.5 A4,4 0 0 1 6,0.5 Z" fill="var(--orange-light)"/><circle cx="6" cy="4.5" r="1.5" fill="var(--orange)"/></svg>24 Mill Lane, Brookmere</span>
    <span class="contact" style="left:375px;top:980px"><svg viewBox="0 0 12 12" fill="none" stroke="var(--orange-light)" stroke-width="1"><circle cx="6" cy="6" r="5"/><ellipse cx="6" cy="6" rx="2.2" ry="5"/><path d="M1,6 H11 M2,3.3 H10 M2,8.7 H10"/></svg>www.brookmereosteopathy.example</span>
    <span class="contact" style="left:375px;top:1004px"><svg viewBox="0 0 12 12"><rect x="0.5" y="2" width="11" height="8" fill="var(--orange-light)"/><path d="M0.5,2 L6,6.5 L11.5,2" fill="none" stroke="var(--orange)" stroke-width="1"/></svg>info@brookmereosteopathy.example</span>
  </address>
</main>
</body>
</html>
```